Velvet Pressings Techno Label Business Card

I'm looking for a very clean business card for my Velvet Pressings music label. The label focusses on techno music. The card should include:

• my name : Tomas Brandt as "Founder & CEO"
• email address: tomas@velvet-pressings.example
• web: www.velvet-pressings.example
• facebook logo + /velvetpress
• twitter logo + /velvetpress
• soundcloud logo + /velvetpressings

Feel free to include your ideas! I'm looking forward to discuss about it.

Tomas

Industry/Entity Type

Business

Contact Information for Business Card

I don't like glossy cards. Prefer matt.

Requirements
Nice to have
• Maybe on one side the complete logo, other side just the icon.
Should not have
• Flashy stuff. Must be clean and business like style.

```html
<!DOCTYPE html>
<html lang="en">
<head>
<meta charset="utf-8">
<title>Velvet Pressings – Business Card</title>
<link rel="stylesheet" href="https://fonts.googleapis.com/css2?family=Ubuntu:wght@400;500;700&display=swap">
<style>
  :root {
    --bg: #e9e7e3;
    --card: #ffffff;
    --card-shade: #f1f1f1;
    --orange: #f26a16;
    --ink: #55575b;
    --ink-soft: #6d6f73;
    --stripe: #56585c;
  }
  * { box-sizing: border-box; margin: 0; padding: 0; }
  html, body { width: 1200px; height: 894px; overflow: hidden; }
  body {
    background: var(--bg);
    font-family: "Ubuntu", "Helvetica Neue", Arial, sans-serif;
    position: relative;
  }
  .card {
    position: absolute;
    left: 280px;
    width: 640px;
    height: 366px;
    border-radius: 22px;
    background: linear-gradient(160deg, var(--card) 40%, var(--card-shade));
    box-shadow: 0 6px 18px rgba(0,0,0,0.12);
    overflow: hidden;
  }
  .card--front { top: 40px; }
  .card--back { top: 446px; }

  .brand {
    position: absolute;
    left: 44px;
    top: 30px;
    display: flex;
    align-items: center;
    gap: 12px;
  }
  .brand__dot {
    width: 30px; height: 30px;
    border-radius: 50%;
    background: var(--orange);
  }
  .brand__name {
    font-size: 28px;
    font-weight: 500;
    color: var(--ink);
    letter-spacing: -0.3px;
  }

  .name-band {
    position: absolute;
    left: 0;
    top: 84px;
    width: 340px;
    height: 72px;
    background: var(--orange);
    border-radius: 0 36px 36px 0;
    color: #fff;
    padding: 12px 0 0 44px;
  }
  .name-band__name {
    font-size: 27px;
    font-weight: 700;
    letter-spacing: 0.5px;
    line-height: 1.1;
  }
  .name-band__title {
    font-size: 14px;
    font-weight: 400;
    letter-spacing: 1px;
    margin-top: 3px;
  }

  .contacts {
    position: absolute;
    top: 174px;
    list-style: none;
  }
  .contacts--main { left: 44px; }
  .contacts--social { left: 430px; }
  .contacts__item {
    display: flex;
    align-items: center;
    gap: 12px;
    height: 25px;
    font-size: 15px;
    color: var(--ink-soft);
    letter-spacing: 0.3px;
    white-space: nowrap;
  }
  .contacts__item--wrap { height: auto; align-items: flex-start; line-height: 20px; }
  .contacts__item--wrap .icon { margin-top: 1px; }
  .icon { width: 18px; height: 18px; flex: none; }
  .social-dot {
    width: 18px; height: 18px;
    flex: none;
    border-radius: 50%;
    background: var(--orange);
  }

  .stripe {
    position: absolute;
    left: 0; right: 0; bottom: 0;
    height: 24px;
    background: var(--stripe);
  }
</style>
</head>
<body>

<section class="card card--front" aria-label="Business card front">
  <div class="brand">
    <span class="brand__dot"></span>
    <span class="brand__name">Velvet Pressings</span>
  </div>

  <div class="name-band">
    <div class="name-band__name">TOMAS BRANDT</div>
    <div class="name-band__title">FOUNDER &amp; CEO</div>
  </div>

  <ul class="contacts contacts--main">
    <li class="contacts__item">
      <svg class="icon" viewBox="0 0 18 18"><circle cx="9" cy="9" r="8" fill="none" stroke="var(--orange)" stroke-width="1.5"/><rect x="6" y="5" width="6" height="8" rx="1" fill="none" stroke="var(--orange)" stroke-width="1.3"/></svg>
      (021) 555 0142
    </li>
    <li class="contacts__item">
      <svg class="icon" viewBox="0 0 18 18"><circle cx="9" cy="9" r="8" fill="none" stroke="var(--orange)" stroke-width="1.5"/><path d="M6 5.5c0 4 2.5 6.5 6.5 6.5l0-2-2-.5-1 1c-1-.5-2-1.5-2.5-2.5l1-1-.5-2z" fill="var(--orange)"/></svg>
      (021) 555 0142
    </li>
    <li class="contacts__item">
      <svg class="icon" viewBox="0 0 18 18"><circle cx="9" cy="9" r="8" fill="var(--orange)"/><circle cx="9" cy="9" r="2.3" fill="none" stroke="#fff" stroke-width="1.3"/><path d="M11.3 9v1a1.4 1.4 0 0 0 2.8 0V9A5 5 0 1 0 11 13" fill="none" stroke="#fff" stroke-width="1.2"/></svg>
      TOMAS@VELVET-PRESSINGS.EXAMPLE
    </li>
    <li class="contacts__item">
      <svg class="icon" viewBox="0 0 18 18"><circle cx="9" cy="9" r="8" fill="var(--orange)"/><circle cx="9" cy="9" r="4.5" fill="none" stroke="#fff" stroke-width="1.1"/><path d="M4.5 9h9M9 4.5c-2 2.5-2 6.5 0 9M9 4.5c2 2.5 2 6.5 0 9" fill="none" stroke="#fff" stroke-width="1"/></svg>
      WWW.VELVET-PRESSINGS.EXAMPLE
    </li>
    <li class="contacts__item contacts__item--wrap">
      <svg class="icon" viewBox="0 0 18 18"><circle cx="9" cy="9" r="8" fill="var(--orange)"/><path d="M9 14s-3.5-4-3.5-6.3a3.5 3.5 0 0 1 7 0C12.5 10 9 14 9 14z" fill="#fff"/><circle cx="9" cy="7.7" r="1.2" fill="var(--orange)"/></svg>
      <span>1030 HARLOW AVE,<br>NORTHFIELD, USA</span>
    </li>
  </ul>

  <ul class="contacts contacts--social">
    <li class="contacts__item"><span class="social-dot"></span>/velvetpress</li>
    <li class="contacts__item"><span class="social-dot"></span>/velvetpress</li>
    <li class="contacts__item"><span class="social-dot"></span>/velvetpressings</li>
  </ul>

  <div class="stripe"></div>
</section>

<section class="card card--back" aria-label="Business card back"></section>

</body>
</html>
```